Business Card Design Project

Doctor, Pain Management. Need a new business card design with appointment info on the back. New address is 18 Corvell Road, Suite 304, Brisdale, NJ 07391. Right now I believe the rest of the information is staying the same.

```html
<!DOCTYPE html>
<html lang="en">
<head>
<meta charset="utf-8">
<title>Kindwell Pain Management – Business Card</title>
<link rel="stylesheet" href="https://fonts.googleapis.com/css2?family=Open+Sans:wght@400;600;700&display=swap">
<style>
  :root {
    --backdrop: #2b2b2d;
    --orange: #ee5a0c;
    --card-white: #ffffff;
    --card-dark: #151515;
    --ink: #333333;
    --ink-soft: #555555;
    --rule: #c9c9c9;
    --light-text: #d6d6d6;
    --muted-text: #b5b5b5;
  }
  * { box-sizing: border-box; margin: 0; padding: 0; }
  html, body { width: 1200px; height: 900px; overflow: hidden; }
  body {
    background: var(--backdrop);
    font-family: "Open Sans", Arial, sans-serif;
    position: relative;
  }
  .card {
    position: absolute;
    left: 320px;
    width: 560px;
    height: 320px;
    border-bottom: 10px solid var(--orange);
    overflow: hidden;
  }
  /* Appointment side */
  .card--appointment { top: 100px; background: var(--card-white); }
  .brand {
    position: absolute;
    top: 48px;
    right: 44px;
    color: var(--orange);
    font-weight: 600;
    font-size: 26px;
    line-height: 1.2;
    white-space: nowrap;
  }
  .appt-fields { position: absolute; left: 40px; right: 40px; top: 112px; }
  .appt-field {
    height: 44px;
    border-bottom: 1px solid var(--rule);
    font-size: 20px;
    color: var(--ink-soft);
    display: flex;
    align-items: flex-end;
    padding-bottom: 4px;
  }
  .appt-note {
    position: absolute;
    left: 40px;
    bottom: 20px;
    font-size: 13px;
    color: var(--ink);
  }
  /* Contact side */
  .card--contact { top: 470px; background: var(--card-dark); text-align: center; }
  .doctor {
    margin-top: 34px;
    color: var(--orange);
    font-weight: 700;
    font-size: 20px;
    text-transform: uppercase;
    letter-spacing: 0.5px;
  }
  .doctor__title { color: var(--muted-text); font-size: 15px; margin-top: 2px; }
  .icon-row {
    display: flex;
    align-items: center;
    justify-content: center;
    gap: 6px;
    margin: 12px auto 6px;
  }
  .icon-row__rule { width: 70px; height: 1px; background: var(--muted-text); }
  .icon-row svg { width: 22px; height: 22px; display: block; }
  .contact-list { list-style: none; color: var(--light-text); font-size: 15px; line-height: 1.35; }
  .divider { width: 230px; height: 1px; background: var(--muted-text); margin: 8px auto; }
  .address { color: var(--light-text); font-size: 15px; line-height: 1.35; font-style: normal; }
</style>
</head>
<body>

<section class="card card--appointment">
  <div class="brand">Kindwell Pain Management</div>
  <div class="appt-fields">
    <div class="appt-field">Name:</div>
    <div class="appt-field">Date :</div>
    <div class="appt-field">Time :</div>
  </div>
  <p class="appt-note">If unable to keep your appointment, please contact us as soon as possible</p>
</section>

<section class="card card--contact">
  <h1 class="doctor">Dr. Lanying Zhou, M.D., Ph.D.</h1>
  <p class="doctor__title">Board Certified Anesthiologist</p>

  <div class="icon-row">
    <span class="icon-row__rule"></span>
    <svg viewBox="0 0 22 22" aria-label="Phone"><rect width="22" height="22" fill="#ee5a0c"/><path d="M6 7c0-1 1-2 2-2h6c1 0 2 1 2 2v1h-3V7h-4v1H6z M7 10h8l1 6H6z" fill="#151515"/></svg>
    <svg viewBox="0 0 22 22" aria-label="Fax"><rect width="22" height="22" fill="#ee5a0c"/><rect x="7" y="4" width="8" height="5" fill="#151515"/><rect x="4" y="9" width="14" height="6" fill="#151515"/><rect x="7" y="13" width="8" height="5" fill="#151515"/></svg>
    <svg viewBox="0 0 22 22" aria-label="Website"><rect width="22" height="22" fill="#ee5a0c"/><circle cx="11" cy="11" r="6.5" fill="none" stroke="#151515" stroke-width="1.6"/><path d="M4.5 11h13M11 4.5c-3 3.5-3 9.5 0 13M11 4.5c3 3.5 3 9.5 0 13" fill="none" stroke="#151515" stroke-width="1.2"/></svg>
    <svg viewBox="0 0 22 22" aria-label="Email"><rect width="22" height="22" fill="#ee5a0c"/><rect x="4" y="6" width="14" height="10" fill="#151515"/><path d="M4.5 6.5 11 12l6.5-5.5" fill="none" stroke="#ee5a0c" stroke-width="1.2"/></svg>
    <span class="icon-row__rule"></span>
  </div>

  <ul class="contact-list">
    <li>973.555.0142</li>
    <li>973.555.0178</li>
    <li>www.kindwellpm.com</li>
    <li>care.kindwellpm@mailbox.com</li>
  </ul>
  <div class="divider"></div>
  <address class="address">18 Corvell Road, Suite 304<br>Brisdale, NJ 07391</address>
</section>

</body>
</html>
```